Kitchen and custom cabinetry company looking for business card design

We make: * Custom Kitchens, contemporary and traditional kitchens, Vanities, Libraries, Custom Entry Doors, Custom Wine Cellars and Custom Design Furniture. Phone number 555-284-7716. Address: Westhampton NY. Email: KAVRO@mailbox.example Portfolio at: KAVROcabinetry.example I would like moderns fonts and not heavy lines. double side but maybe will use clear plastic. I attached the logo.

Industry/Entity Type

Business

```html
<!DOCTYPE html>
<html lang="en">
<head>
<meta charset="utf-8">
<title>Kavro Cabinetry – Business Card</title>
<link href="https://fonts.googleapis.com/css2?family=Questrial&display=swap" rel="stylesheet">
<style>
  :root {
    --orange: #f15a29;
    --orange-light: #f5845f;
    --grey: #848484;
    --grey-light: #bcbcbc;
    --brand-grey: #7d7d7d;
    --white: #ffffff;
    --backdrop: #e9e6e2;
  }
  * { margin: 0; padding: 0; box-sizing: border-box; }
  html, body {
    width: 1200px; height: 970px; overflow: hidden;
    background: var(--backdrop);
    font-family: "Questrial", Arial, sans-serif;
  }
  .sheet { position: relative; width: 1200px; height: 970px; }
  .card {
    position: absolute; top: 126px;
    width: 409px; height: 716px;
    display: flex; flex-direction: column;
  }
  .card--front { left: 149px; --accent: var(--orange); --accent-soft: var(--orange-light); }
  .card--back  { left: 634px; --accent: var(--grey);   --accent-soft: var(--grey-light); }

  .card__cap { height: 30px; background: var(--accent); border-radius: 16px 16px 0 0; }
  .card__brand-panel {
    height: 268px; background: var(--white);
    display: flex; align-items: center; justify-content: center;
  }
  .brand-name {
    font-size: 36px; line-height: 1; letter-spacing: 3px;
    color: var(--brand-grey);
    text-transform: uppercase;
  }
  .card__gap { height: 26px; }
  .card__stripe { height: 48px; background: var(--accent-soft); }
  .card__gap--low { height: 23px; }
  .card__body {
    flex: 1; background: var(--accent);
    border-radius: 0 0 22px 22px;
    color: var(--white); text-align: right;
    padding: 48px 40px 0 20px;
  }
  .person-name { font-size: 25px; letter-spacing: 1.2px; line-height: 1.1; }
  .person-role { font-size: 16px; letter-spacing: 1px; opacity: 0.9; }
  .contact { margin-top: 32px; font-size: 18px; letter-spacing: 0.8px; line-height: 1.17; }
  .address { margin-top: 36px; font-size: 18px; letter-spacing: 0.8px; line-height: 1.2; }

  .card--back .card__body { padding-right: 33px; }
  .services {
    list-style: none; margin-top: 22px;
    font-size: 20.5px; letter-spacing: 1.7px; line-height: 28.4px;
  }
</style>
</head>
<body>
<main class="sheet">
  <section class="card card--front" aria-label="Card front">
    <div class="card__cap"></div>
    <div class="card__brand-panel">
      <div class="brand-name">Kavro Cabinetry</div>
    </div>
    <div class="card__gap"></div>
    <div class="card__stripe"></div>
    <div class="card__gap--low"></div>
    <div class="card__body">
      <p class="person-name">Marco Ellison</p>
      <p class="person-role">Owner</p>
      <p class="contact">555&nbsp;&nbsp;284&nbsp;&nbsp;7716<br>kavro@mailbox.example<br>www.kavrocabinetry.example</p>
      <p class="address">2290 Harbor Mill rd.<br>Westhampton, NY. 11977</p>
    </div>
  </section>

  <section class="card card--back" aria-label="Card back">
    <div class="card__cap"></div>
    <div class="card__brand-panel">
      <div class="brand-name">Kavro Cabinetry</div>
    </div>
    <div class="card__gap"></div>
    <div class="card__stripe"></div>
    <div class="card__gap--low"></div>
    <div class="card__body">
      <ul class="services">
        <li>CONTEMPORAY KITCHENS</li>
        <li>TRADITIONAL KITCHENS</li>
        <li>VANITIES</li>
        <li>LIBRARIES</li>
        <li>CUSTOM WINE CELLARS</li>
        <li>CUSTOM DESIGN FURNITURE</li>
      </ul>
    </div>
  </section>
</main>
</body>
</html>
```